Stationery for a private security company, "Brenmoor Security Services Ltd."

Needed is a stationery design for a private security company. The designs must show professionalism and that our company mean nothing but business. Watermark of the company logo on the letterhead page is also a must. The final design must represent innovation and professionalism. It would be great if designers could integrate the colours black and silver onto the cards and letterheads..

Thank you

```html
<!DOCTYPE html>
<html lang="en">
<head>
<meta charset="utf-8">
<title>Brenmoor Security Services Ltd. — Letterhead</title>
<link href="https://fonts.googleapis.com/css2?family=Cinzel:wght@600&family=Lato:wght@400&display=swap" rel="stylesheet">
<style>
  :root {
    --backdrop: #e4e4e4;
    --page-light: #f4f4f4;
    --page-mid: #dadada;
    --page-dark: #bfbfbf;
    --ink: #111111;
    --silver: #9a9a9a;
    --silver-light: #c8c8c8;
    --watermark: #6e6e6e;
    --rule: #6f6f6f;
  }
  * { margin: 0; padding: 0; box-sizing: border-box; }
  html, body {
    width: 1200px;
    height: 983px;
    overflow: hidden;
    background: var(--backdrop);
  }
  .canvas { position: relative; width: 1200px; height: 983px; }
  .letterhead {
    position: absolute;
    left: 280px;
    top: 76px;
    width: 640px;
    height: 830px;
    background: linear-gradient(180deg, var(--page-light) 0%, var(--page-mid) 55%, var(--page-dark) 100%);
    box-shadow: 0 10px 30px rgba(0,0,0,0.18);
    overflow: hidden;
  }
  .margin-band { position: absolute; top: 0; bottom: 0; }
  .margin-band--silver { left: 20px; width: 22px; background: linear-gradient(180deg, var(--silver-light), var(--silver)); }
  .margin-band--black { left: 46px; width: 11px; background: var(--ink); }
  .margin-band--hairline-a { left: 62px; width: 2px; background: var(--silver); }
  .margin-band--hairline-b { left: 68px; width: 1px; background: var(--rule); }
  .margin-band--hairline-c { left: 74px; width: 1px; background: var(--silver-light); }

  .watermark-name {
    position: absolute;
    left: 150px;
    top: 250px;
    font-family: "Cinzel", serif;
    font-weight: 600;
    font-size: 68px;
    letter-spacing: 4px;
    line-height: 1;
    color: var(--watermark);
    opacity: 0.35;
    white-space: nowrap;
  }

  .brand {
    position: absolute;
    left: 110px;
    top: 548px;
    display: flex;
    align-items: center;
    gap: 12px;
  }
  .brand-square {
    width: 22px;
    height: 22px;
    background: var(--ink);
  }
  .brand-name {
    font-family: "Cinzel", serif;
    font-weight: 600;
    color: var(--ink);
    line-height: 1.1;
  }
  .brand-name__main { display: block; font-size: 24px; letter-spacing: 3px; }
  .brand-name__sub { display: block; font-size: 11px; letter-spacing: 1px; }

  .footer-rule {
    position: absolute;
    left: 290px;
    right: 40px;
    top: 592px;
    height: 1px;
    background: var(--rule);
  }
  .web-address {
    position: absolute;
    right: 40px;
    top: 662px;
    padding-bottom: 6px;
    border-bottom: 1px solid var(--rule);
    font-family: "Lato", sans-serif;
    font-size: 12px;
    color: var(--ink);
  }
</style>
</head>
<body>
<div class="canvas">
  <div class="letterhead">
    <div class="margin-band margin-band--silver"></div>
    <div class="margin-band margin-band--black"></div>
    <div class="margin-band margin-band--hairline-a"></div>
    <div class="margin-band margin-band--hairline-b"></div>
    <div class="margin-band margin-band--hairline-c"></div>

    <p class="watermark-name" aria-hidden="true">BRENMOOR</p>

    <div class="brand">
      <span class="brand-square"></span>
      <p class="brand-name">
        <span class="brand-name__main">Brenmoor</span>
        <span class="brand-name__sub">Security Services Ltd.</span>
      </p>
    </div>
    <div class="footer-rule"></div>
    <p class="web-address">www.brenmoorsecurity.com</p>
  </div>
</div>
</body>
</html>
```